Property management company looking for modern card design

We at Blue Heron Partners provides property management services for its residential and commercial properties, with expertise in all categories of multifamily, industrial and office projects throughout California.

We need a business card design that is professional and modern designed business card. In our field, clients get hundreds of business cards, we would like our card to stand out.

Please avoid small print.

Target Market(s)

Professionals and high end clients

Industry/Entity Type

Financial Planning

Contact Information for Business Card

Company Name: Blue Heron Partners, Name, email, license #, phone number, website blueheronpartners.com

Font styles to use
Sans Serif

Requirements
Must have
• The card design needs to be adaptable because there is a possibly we will be expanding into different sectors other than real estate. The card design should be focused on financial planning and asset management.
Nice to have
• Modern and simple business card. Eye catching. Non-standard size/shaped cards would be great.
• blueheronpartners.com
Should not have
• Too many bright color or any pictures or shapes of real estate stuff.

```html
<!DOCTYPE html>
<html lang="en">
<head>
<meta charset="utf-8">
<title>Blue Heron Partners – Business Card</title>
<link rel="stylesheet" href="https://fonts.googleapis.com/css2?family=Open+Sans:wght@400;600&display=swap">
<style>
  :root {
    --backdrop: #869a98;
    --paper: #e8eeec;
    --ink-deep: #181b1c;
    --ink-slate: #2c3234;
    --ink-steel: #3d4649;
    --ink-panel: #252a2c;
    --red-bright: #c4000c;
    --red-deep: #6f0000;
    --red-fold: #8a0008;
    --red-mark: #b0000f;
    --text-light: #f2f2f2;
  }
  html, body {
    margin: 0;
    padding: 0;
    width: 1200px;
    height: 1200px;
    overflow: hidden;
    background: var(--backdrop);
  }
  .canvas { display: block; width: 1200px; height: 1200px; }
  .brand-name {
    font-family: "Open Sans", sans-serif;
    font-weight: 600;
    fill: var(--red-bright);
    letter-spacing: 4px;
  }
  .contact-label {
    font-family: "Open Sans", sans-serif;
    font-weight: 400;
    fill: var(--text-light);
    font-size: 29px;
  }
  .contact-label.is-name { font-weight: 600; }
  .strip-deep { fill: var(--ink-deep); }
  .strip-slate { fill: var(--ink-slate); }
  .strip-steel { fill: var(--ink-steel); }
  .panel-dark { fill: var(--ink-panel); }
  .paper { fill: var(--paper); }
  .ribbon-deep { fill: var(--red-deep); }
  .ribbon-bright { fill: var(--red-bright); }
  .ribbon-fold { fill: var(--red-fold); }
  .brand-dot { fill: var(--red-mark); }
  .icon { fill: var(--ink-panel); }
  .icon-line { fill: none; stroke: var(--ink-panel); stroke-width: 2.5; }
</style>
</head>
<body>
<svg class="canvas" viewBox="0 0 1500 1500" xmlns="http://www.w3.org/2000/svg">

  <!-- Front of card -->
  <g class="card card-front">
    <rect class="paper" x="305" y="183" width="832" height="474"/>
    <rect class="strip-deep" x="305" y="183" width="79" height="474"/>
    <rect class="strip-slate" x="384" y="183" width="52" height="474"/>
    <rect class="strip-slate" x="1011" y="183" width="50" height="474"/>
    <rect class="strip-deep" x="1061" y="183" width="76" height="474"/>

    <g class="edge-ribbons">
      <rect class="ribbon-deep" x="305" y="238" width="79" height="52"/>
      <polygon class="ribbon-bright" points="384,238 448,252 448,300 384,290"/>
      <polygon class="ribbon-fold" points="436,298 448,300 436,312"/>

      <rect class="ribbon-deep" x="305" y="345" width="79" height="51"/>
      <polygon class="ribbon-bright" points="384,345 448,358 448,406 384,396"/>
      <polygon class="ribbon-fold" points="436,404 448,406 436,418"/>

      <rect class="ribbon-deep" x="305" y="451" width="79" height="51"/>
      <polygon class="ribbon-bright" points="384,451 448,464 448,512 384,502"/>
      <polygon class="ribbon-fold" points="436,510 448,512 436,524"/>

      <rect class="ribbon-deep" x="305" y="550" width="79" height="51"/>
      <polygon class="ribbon-bright" points="384,550 448,563 448,611 384,601"/>
      <polygon class="ribbon-fold" points="436,609 448,611 436,623"/>
    </g>

    <g class="buckle">
      <polygon class="ribbon-fold" points="991,368 1011,348 1011,368"/>
      <polygon class="ribbon-fold" points="991,472 1011,472 1011,492"/>
      <rect class="ribbon-bright" x="991" y="368" width="127" height="104"/>
      <rect class="ribbon-deep" x="1011" y="390" width="92" height="62"/>
    </g>

    <g class="brand">
      <circle class="brand-dot" cx="722" cy="390" r="80"/>
      <text class="brand-name" x="722" y="520" font-size="42" text-anchor="middle">BLUE HERON</text>
      <text class="brand-name" x="722" y="570" font-size="42" text-anchor="middle">PARTNERS</text>
    </g>
  </g>

  <!-- Back of card -->
  <g class="card card-back">
    <rect class="paper" x="305" y="795" width="832" height="478"/>
    <rect class="strip-deep" x="305" y="795" width="42" height="478"/>
    <rect class="strip-slate" x="347" y="795" width="27" height="478"/>

    <g class="edge-ribbons">
      <rect class="ribbon-deep" x="305" y="856" width="42" height="51"/>
      <polygon class="ribbon-bright" points="347,856 381,866 381,918 347,907"/>
      <rect class="ribbon-deep" x="305" y="958" width="42" height="51"/>
      <polygon class="ribbon-bright" points="347,958 381,968 381,1020 347,1009"/>
      <rect class="ribbon-deep" x="305" y="1065" width="42" height="51"/>
      <polygon class="ribbon-bright" points="347,1065 381,1075 381,1127 347,1116"/>
      <rect class="ribbon-deep" x="305" y="1165" width="42" height="52"/>
      <polygon class="ribbon-bright" points="347,1165 381,1175 381,1228 347,1217"/>
    </g>

    <rect class="strip-steel" x="721" y="795" width="67" height="478"/>
    <rect class="panel-dark" x="788" y="795" width="349" height="478"/>

    <g class="brand">
      <circle class="brand-dot" cx="548" cy="1006" r="63"/>
      <text class="brand-name" x="548" y="1112" font-size="33" text-anchor="middle">BLUE HERON</text>
      <text class="brand-name" x="548" y="1152" font-size="33" text-anchor="middle">PARTNERS</text>
    </g>

    <g class="contact-row">
      <rect class="ribbon-deep" x="788" y="833" width="349" height="55"/>
      <polygon class="ribbon-bright" points="708,855 788,833 788,888 721,900 708,900"/>
      <polygon class="ribbon-fold" points="708,900 721,900 721,912"/>
      <circle class="icon" cx="755" cy="868" r="19"/>
      <circle fill="#c4000c" cx="755" cy="863" r="5"/>
      <path fill="#c4000c" d="M746,876 q9,-10 18,0 z"/>
      <text class="contact-label is-name" x="937" y="868" text-anchor="middle">Individual Name</text>
    </g>

    <g class="contact-row">
      <rect class="ribbon-deep" x="788" y="944" width="349" height="55"/>
      <polygon class="ribbon-bright" points="708,966 788,944 788,999 721,1011 708,1011"/>
      <polygon class="ribbon-fold" points="708,1011 721,1011 721,1023"/>
      <path class="icon" d="M744,962 l8,-3 6,11 -5,4 q4,9 12,13 l4,-5 11,6 -3,8 q-20,2 -33,-34 z"/>
      <text class="contact-label" x="937" y="980" text-anchor="middle">Phone</text>
    </g>

    <g class="contact-row">
      <rect class="ribbon-deep" x="788" y="1056" width="349" height="55"/>
      <polygon class="ribbon-bright" points="708,1078 788,1056 788,1111 721,1123 708,1123"/>
      <polygon class="ribbon-fold" points="708,1123 721,1123 721,1135"/>
      <g class="icon-line">
        <circle cx="753" cy="1092" r="16"/>
        <ellipse cx="753" cy="1092" rx="7" ry="16"/>
        <line x1="737" y1="1092" x2="769" y2="1092"/>
        <line x1="740" y1="1084" x2="766" y2="1084"/>
        <line x1="740" y1="1100" x2="766" y2="1100"/>
      </g>
      <text class="contact-label" x="937" y="1092" text-anchor="middle">E-mail</text>
    </g>

    <g class="contact-row">
      <rect class="ribbon-deep" x="788" y="1170" width="349" height="55"/>
      <polygon class="ribbon-bright" points="708,1192 788,1170 788,1225 721,1237 708,1237"/>
      <polygon class="ribbon-fold" points="708,1237 721,1237 721,1249"/>
      <path class="icon" d="M762,1186 a9,9 0 0 1 9,9 q0,7 -9,16 q-9,-9 -9,-16 a9,9 0 0 1 9,-9 z"/>
      <circle fill="#c4000c" cx="762" cy="1195" r="3.5"/>
      <polygon class="icon" points="736,1206 752,1206 750,1214 734,1214"/>
      <polygon class="icon" points="734,1216 772,1216 770,1222 732,1222"/>
      <text class="contact-label" x="951" y="1206" text-anchor="middle">Address</text>
    </g>
  </g>
</svg>
</body>
</html>
```